Audio/ Video Packaging Design for a Technology company.

We need a packaging design for a bag that is 7" wide and 10" high. The design will be for a new line of audio/video products. We would like to see designs that represent a superior quality product that provides a pure connection. We want the equivalent of a nice retail bag that you would find in a store like Tallow Mart. It should be a maximum of three colors. We really want something sharp, professional and eye catching, not whimsical or cartoonish. I've included a couple of examples below. I don't really like the designs of the bags, but I want you to see examples of what I'm looking for.

The company logo, which is uploaded, should be on the design. The words "audio and video products" should be either underneath the logo or to the side. Also, somewhere on the bag, we would like the words "For a Pure Connection"

The winner of this contest will likely get the opportunity for additional work as we have more products ready to launch.

Target Market(s)

resellers, consumers - men 25-60

Industry/Entity Type

It Company

Requirements
Must have
• It should be a maximum of three colors. We really want something sharp, professional and eye catching, not whimsical or cartoonish
Nice to have
• Eye-catching design. Utilize the entire bag but don't make it too busy.
Should not have
• Whimsical, cartoonish

```html
<!DOCTYPE html>
<html lang="en">
<head>
<meta charset="utf-8">
<title>Quellor — Audio and Video Packaging</title>
<link href="https://fonts.googleapis.com/css2?family=Montserrat:wght@400;500&family=Quicksand:wght@500&display=swap" rel="stylesheet">
<style>
  :root {
    --backdrop: #9c9c9e;
    --card-white: #ffffff;
    --panel-dark: #3c3c3e;
    --accent-blue: #4cc4ee;
    --trace-tint: #eceef0;
    --window-light: #d9d9d9;
    --window-dark: #4a4a4a;
    --fine-print: #9a9a9a;
  }
  * { margin: 0; padding: 0; box-sizing: border-box; }
  html, body {
    width: 1200px; height: 960px; overflow: hidden;
    background: var(--backdrop);
  }
  .package {
    position: absolute; left: 298px; top: 35px;
    width: 603px; height: 890px;
    border-radius: 30px; overflow: hidden;
    background: var(--card-white);
    font-family: "Montserrat", sans-serif;
  }
  .package-art { position: absolute; inset: 0; width: 603px; height: 890px; }
  .brand {
    position: absolute; right: 28px; top: 678px;
    display: flex; align-items: center; gap: 18px;
  }
  .brand-dot { width: 40px; height: 40px; border-radius: 50%; background: var(--accent-blue); }
  .brand-name {
    font-family: "Quicksand", sans-serif; font-weight: 500;
    font-size: 60px; letter-spacing: 2px; color: var(--card-white); line-height: 1;
  }
  .product-line {
    position: absolute; right: 26px; top: 744px;
    font-family: "Quicksand", sans-serif; font-weight: 500;
    font-size: 20px; letter-spacing: 3.2px; color: var(--accent-blue);
  }
  .tagline {
    position: absolute; right: 26px; top: 802px;
    font-size: 27px; font-weight: 500; color: var(--card-white);
  }
  .origin {
    position: absolute; left: 30px; top: 848px;
    transform: rotate(-90deg); transform-origin: left top;
    font-size: 11px; letter-spacing: 0.5px; color: var(--fine-print);
    white-space: nowrap;
  }
</style>
</head>
<body>
  <main class="package">
    <svg class="package-art" viewBox="0 0 603 890" xmlns="http://www.w3.org/2000/svg">
      <defs>
        <linearGradient id="window-fill" x1="0" y1="0" x2="1" y2="1">
          <stop offset="0" stop-color="var(--window-light)"/>
          <stop offset="0.5" stop-color="#8a8a8a"/>
          <stop offset="1" stop-color="var(--window-dark)"/>
        </linearGradient>
      </defs>
      <!-- hanger slot -->
      <g class="hang-slot" fill="var(--backdrop)">
        <rect x="231" y="34" width="142" height="36" rx="18"/>
        <circle cx="302" cy="38" r="20"/>
      </g>
      <!-- circuit trace areas -->
      <rect class="trace-area" x="0" y="140" width="115" height="200" fill="var(--trace-tint)" role="img" aria-label="Circuit board trace pattern"/>
      <rect class="trace-area" x="470" y="50" width="133" height="250" fill="var(--trace-tint)" role="img" aria-label="Circuit board trace pattern"/>
      <!-- product window -->
      <rect class="product-window" x="118" y="178" width="363" height="420" rx="26" fill="url(#window-fill)" role="img" aria-label="Clear window showing the coiled cable and connector inside"/>
      <!-- lower V panel -->
      <polygon class="band-blue" points="0,317 355,545 603,235 603,290 360,600 0,345" fill="var(--accent-blue)"/>
      <polygon class="band-white" points="0,345 360,575 603,262 603,292 365,632 0,362" fill="var(--card-white)"/>
      <polygon class="panel-dark" points="0,362 365,632 603,292 603,890 0,890" fill="var(--panel-dark)"/>
    </svg>

    <div class="brand">
      <span class="brand-dot"></span>
      <span class="brand-name">QUELLOR</span>
    </div>
    <p class="product-line">audio and video products</p>
    <p class="tagline">“For a Pure Connection”</p>
    <p class="origin">MADE IN CHINA</p>
  </main>
</body>
</html>
```